Business Card Design Project

Business Card design based on logo.
Updates

I need business card, letterhead, envelope, and if possible, Powerpoint slide template.

On front of business card: Just logo- and  my name and title:  Harriet Lindqvist, Principal

On reverse-logo and the rest of the contact info:

4871 Quarry Lane
Alder Springs, CA 95734
650-318-2764
hl@brackenstudyworks.example

On letterhead-Just logo at top, at bottom  the rest-very small along the bottom

On PPT slide-just the logo.

I also want to try a few other colors-I like lime/dark grey (not black) but would like to try Sienna, maybe also indigo or bright blue-green.

I forgot to add-

On the business card-switch to vertical on reverse side and put:

Reverse side-switch to vertical and list:

Harriet Lindqvist
Principal
Bracken Study Works, LLC

650-318-2764

4871 Quarry Lane
Alder Springs, CA 95734

Harriet Lindqvist
Principal

650-318-2764

4871 Quarry Lane
Alder Springs, CA 95734

I have another project at the same time-for Stationery. Feel free to submit to that one also.

That one includes letterhead, envelope, PPT slide, folder cover sheet-HL

Industry/Entity Type

Business

Requirements
Must have
• Must use logo-preferably lime green version-with gray, not black or just 2-tone -logo on colored background.

```html
<!DOCTYPE html>
<html lang="en">
<head>
<meta charset="utf-8">
<title>Bracken Study Works — Business Card</title>
<link rel="stylesheet" href="https://fonts.googleapis.com/css2?family=Source+Sans+3:wght@400;600&display=swap">
<style>
  :root {
    --page: #ececec;
    --card-white: #eeeeee;
    --lime: #7aa01f;
    --lime-text: #7aa51c;
    --grey: #333333;
    --rule: #a8a8a8;
  }
  * { margin: 0; padding: 0; box-sizing: border-box; }
  html, body { width: 1200px; height: 1192px; overflow: hidden; }
  body {
    position: relative;
    background: var(--page);
    font-family: "Source Sans 3", Arial, sans-serif;
    color: var(--grey);
  }
  .card { position: absolute; }
  .card--front { left: 266px; top: 171px; width: 655px; height: 371px; background: var(--card-white); }
  .card--back { left: 265px; top: 656px; width: 653px; height: 370px; background: var(--lime); }

  .brand {
    position: absolute;
    display: flex;
    align-items: center;
    gap: 12px;
    font-weight: 600;
    line-height: 1.05;
  }
  .brand__square { width: 16px; height: 16px; flex: none; }
  .card--front .brand { left: 37px; top: 100px; font-size: 30px; color: var(--grey); }
  .card--front .brand__square { background: var(--lime); }
  .card--back .brand {
    left: 0; right: 0; top: 148px; justify-content: center;
    font-size: 32px; color: var(--grey);
  }
  .card--back .brand__square { background: var(--grey); }

  .holder { position: absolute; right: 35px; top: 188px; text-align: right; }
  .holder__name { font-size: 19px; font-weight: 600; color: var(--lime-text); line-height: 22px; }
  .holder__title { font-size: 15px; line-height: 20px; }

  .rule { position: absolute; left: 37px; right: 35px; top: 234px; height: 1px; background: var(--rule); }

  .contact { position: absolute; top: 265px; font-size: 15px; line-height: 22.5px; font-style: normal; white-space: nowrap; }
  .contact--address { left: 37px; }
  .contact__company { color: var(--lime-text); }
  .contact--reach { left: 259px; }
  .contact__row { display: flex; align-items: center; gap: 8px; }
  .contact__icon { width: 14px; height: 14px; flex: none; }
</style>
</head>
<body>
  <section class="card card--front">
    <div class="brand"><span class="brand__square"></span><span>Bracken<br>Study Works</span></div>

    <div class="holder">
      <p class="holder__name">Harriet Lindqvist</p>
      <p class="holder__title">Principal</p>
    </div>

    <div class="rule"></div>

    <address class="contact contact--address">
      <p class="contact__company">Bracken Study Works, LLC</p>
      <p>4871 Quarry Lane</p>
      <p>Alder Springs, CA 95734</p>
    </address>

    <div class="contact contact--reach">
      <p class="contact__row">
        <svg class="contact__icon" viewBox="0 0 14 14" aria-hidden="true"><path d="M2 4 Q7 0 12 4 L11 6 L9 5 L9 4 Q7 3 5 4 L5 5 L3 6 Z M4 7 L10 7 L12 12 L2 12 Z" fill="#7aa01f"/></svg>
        <span>650-318-2764</span>
      </p>
      <p class="contact__row">
        <svg class="contact__icon" viewBox="0 0 14 14" aria-hidden="true"><text x="7" y="11.5" text-anchor="middle" font-size="13" font-weight="600" fill="#7aa01f" font-family="Arial, sans-serif">@</text></svg>
        <span>hl@brackenstudyworks.example</span>
      </p>
      <p class="contact__row">
        <svg class="contact__icon" viewBox="0 0 14 14" aria-hidden="true"><g fill="none" stroke="#7aa01f" stroke-width="1.4"><circle cx="7" cy="7" r="5.8"/><ellipse cx="7" cy="7" rx="2.6" ry="5.8"/><path d="M1.2 7 H12.8"/></g></svg>
        <span>www.brackenstudyworks.example</span>
      </p>
    </div>
  </section>

  <section class="card card--back">
    <div class="brand"><span class="brand__square"></span><span>Bracken Study Works</span></div>
  </section>
</body>
</html>
```